Brightway Haul & Upkeep Services, are a company that offers a 'one stop shop' pre-move clean up a

I have already selected a logo which I would like on the front of the business cards along with phone numbers, web address and email which are:
0487650392
www.brightwayhaul.com.au
brightwayhaulandupkeep@mailbox.example

On the back of the card I would like to list some of the types of service we offer (clean - move - repairs/maintenance) which are:
CLEAN - windows, gutters, solar panels, driveways/paths, carpets.
MOVE - Small/medium size house/office moves, large item pick-up & delivery, yard clean-up and removal.
General maintenance and repairs.

I would like the blue logo on a gray background.

Thanks

```html
<!DOCTYPE html>
<html lang="en">
<head>
<meta charset="utf-8">
<title>Brightway Haul &amp; Upkeep Services – Business Cards</title>
<link rel="stylesheet" href="https://fonts.googleapis.com/css2?family=Open+Sans:wght@400;600;800&display=swap">
<style>
  :root {
    --backdrop: #e9e6e3;
    --card-grey-light: #f2f2f2;
    --card-grey: #c9c9c9;
    --brand-blue: #2d72c2;
    --rule-dark: #333333;
    --ink: #1f1f1f;
    --white: #ffffff;
  }
  * { box-sizing: border-box; margin: 0; padding: 0; }
  html, body {
    width: 1200px;
    height: 682px;
    overflow: hidden;
  }
  body {
    background: var(--backdrop);
    font-family: "Open Sans", Arial, sans-serif;
    position: relative;
  }
  .card {
    position: absolute;
    top: 186px;
    width: 540px;
    height: 310px;
    overflow: hidden;
    background: radial-gradient(ellipse at 45% 40%, var(--card-grey-light) 0%, var(--card-grey) 100%);
    box-shadow: 0 10px 24px rgba(0,0,0,0.25);
  }
  .card--front { left: 40px; }
  .card--back  { left: 620px; }

  /* Front */
  .front__brand {
    position: absolute;
    left: 40px;
    top: 52px;
    color: var(--brand-blue);
    font-weight: 800;
    text-transform: uppercase;
    line-height: 1.05;
  }
  .front__brand .brand-line-1 { display: block; font-size: 46px; letter-spacing: 0.5px; }
  .front__brand .brand-line-2 { display: block; font-size: 24px; letter-spacing: 0.3px; }
  .front__rule {
    position: absolute;
    left: 0; right: 0;
    top: 188px;
    height: 3px;
    background: var(--rule-dark);
  }
  .front__band {
    position: absolute;
    left: 0; right: 0;
    top: 191px;
    bottom: 0;
    background: var(--brand-blue);
    padding: 20px 0 0 34px;
  }
  .contact-list { list-style: none; }
  .contact-list li {
    display: flex;
    align-items: center;
    gap: 10px;
    color: var(--white);
    font-size: 14px;
    line-height: 1;
    margin-bottom: 14px;
  }
  .contact-list li:first-child { font-size: 15px; }
  .contact-icon { width: 13px; height: 13px; flex: none; }

  /* Back */
  .back__brand {
    position: absolute;
    left: 0; right: 0;
    top: 52px;
    text-align: center;
    color: var(--brand-blue);
    font-weight: 800;
    text-transform: uppercase;
    line-height: 1.05;
  }
  .back__brand .brand-line-1 { display: block; font-size: 44px; }
  .back__brand .brand-line-2 { display: block; font-size: 23px; }
  .services {
    position: absolute;
    left: 0; right: 0;
    top: 168px;
    text-align: center;
  }
  .services__title {
    color: var(--brand-blue);
    font-weight: 600;
    font-size: 21px;
    letter-spacing: 7px;
    margin-bottom: 10px;
  }
  .services__list {
    list-style: none;
    color: var(--ink);
    font-weight: 600;
    font-size: 18px;
    line-height: 1.35;
  }
  .services__list .bullet { color: var(--brand-blue); margin-right: 4px; }
  .services__list .gap { display: inline-block; width: 22px; }
</style>
</head>
<body>

  <section class="card card--front" aria-label="Business card front">
    <h1 class="front__brand">
      <span class="brand-line-1">Brightway Haul</span>
      <span class="brand-line-2">&amp; Upkeep Services</span>
    </h1>
    <div class="front__rule"></div>
    <div class="front__band">
      <ul class="contact-list">
        <li>
          <svg class="contact-icon" viewBox="0 0 16 16" aria-hidden="true">
            <circle cx="8" cy="8" r="7.5" fill="none" stroke="#fff" stroke-width="1"/>
            <path d="M5 4.5c.4-.4.9-.4 1.2 0l.8 1.1c.2.3.2.7-.1 1l-.5.5c.4.9 1.1 1.7 2 2.1l.5-.5c.3-.3.7-.3 1-.1l1.1.8c.4.3.4.8 0 1.2l-.6.6c-2.6.3-5.9-3-5.6-5.6z" fill="#fff"/>
          </svg>
          <span>0487650392</span>
        </li>
        <li>
          <svg class="contact-icon" viewBox="0 0 16 16" aria-hidden="true">
            <rect x="1" y="3.5" width="14" height="9" rx="1" fill="#fff"/>
            <path d="M1.5 4l6.5 5 6.5-5" fill="none" stroke="#2d72c2" stroke-width="1.2"/>
          </svg>
          <span>brightwayhaulandupkeep@mailbox.example</span>
        </li>
        <li>
          <svg class="contact-icon" viewBox="0 0 16 16" aria-hidden="true">
            <circle cx="8" cy="8" r="7" fill="none" stroke="#fff" stroke-width="1.2"/>
            <ellipse cx="8" cy="8" rx="3" ry="7" fill="none" stroke="#fff" stroke-width="1"/>
            <path d="M1 8h14M2.2 4.5h11.6M2.2 11.5h11.6" stroke="#fff" stroke-width="1"/>
          </svg>
          <span>www.brightwayhaul.com.au</span>
        </li>
      </ul>
    </div>
  </section>

  <section class="card card--back" aria-label="Business card back">
    <h2 class="back__brand">
      <span class="brand-line-1">Brightway Haul</span>
      <span class="brand-line-2">&amp; Upkeep Services</span>
    </h2>
    <div class="services">
      <p class="services__title">Services we offer</p>
      <ul class="services__list">
        <li><span class="bullet">•</span>Clean<span class="gap"></span><span class="bullet">•</span>Move</li>
        <li><span class="bullet">•</span>General maintenance and repairs.</li>
      </ul>
    </div>
  </section>

</body>
</html>
```